Fitness website

Website for a fitness brand (see attached specs). Design needs to be modern and vibrant with CTAs on every page. We will provide logos, images, etc but for now user placeholder text and images. For now use the name 'Corvane Athletics' as the name to use on the design. The goal of this site is to either get people to join the gym (5 physical locations across the US); buy an online program; buy merch or supplements or sign up for the newsletter. Pleas use images from this foldeR: https://filebarn.example/share/folders/8QwTz41mKpLrXv93NdYe7HsaBuJ0Cf2_R?usp=sharing

We will be coding this in ReactNative. Lots more work for the winner as well, this is a 1st project for us.

Target Market(s)

fitness enthusiats

Industry/Entity Type

fitness, health, wellness

Number of Pages Required

5+ page

Font styles to use
Other font styles liked:
• Lato

Colors
0054AA
0677BA
7BADD7
CADEEF
E8F1F8
0094D4
00A9DD
6FCCEA
C7EBF8
E9F6FB
00AB8E
00BBA5
67D7C9
C6EFE9
E9F9F6
EE7325
F08F49
F5BC92
FAE3D3
FDF4ED

Requirements
Must have
• must be reactive. most people will view it first on mobile
Nice to have
• video in hero section of top of home page

```html
<!DOCTYPE html>
<html lang="en">
<head>
<meta charset="utf-8">
<title>Corvane Athletics</title>
<link href="https://fonts.googleapis.com/css2?family=Lato:wght@400;700;900&family=Manrope:wght@500;600;700&display=swap" rel="stylesheet">
<style>
:root{
  --green:#1d8f6b;
  --green-dark:#167a5a;
  --green-bright:#2fb37e;
  --navy:#1b3a9c;
  --navy-deep:#173290;
  --ink:#111;
  --text:#333;
  --muted:#555;
  --pale-blue:#e4edf7;
  --mint:#b7e7de;
  --white:#fff;
}
*{box-sizing:border-box;margin:0;padding:0}
html,body{width:1200px;height:4295px;overflow:hidden}
body{font-family:"Lato",sans-serif;color:var(--text);background:var(--white);position:relative}
.abs{position:absolute}
.brand{font-family:"Manrope",sans-serif;font-weight:600;color:var(--ink);font-size:27px}
/* header */
.site-header{position:absolute;left:0;top:0;width:1200px;height:117px;background:var(--white)}
.site-header .brand{left:152px;top:38px}
.search{left:717px;top:20px;width:230px;height:36px;border:1.5px solid var(--green);border-radius:18px;font-size:12px;padding:10px 18px;color:#444}
.search svg{position:absolute;right:12px;top:10px}
.btn{display:inline-flex;align-items:center;justify-content:center;font-weight:900;color:var(--white);background:var(--green);border-radius:30px;text-transform:uppercase}
.shop{left:962px;top:22px;width:88px;height:33px;font-size:14px}
.nav{left:440px;top:76px;display:flex;gap:0;font-size:13px;color:#222;letter-spacing:.3px}
.nav span{position:absolute;white-space:nowrap}
.nav .active{color:var(--green);font-weight:700}
/* hero */
.hero{position:absolute;left:0;top:117px;width:1200px;height:558px;background:linear-gradient(90deg,#2a2a2c,#3b3b3e 35%,#2f3034 60%,#45464a)}
.hero-shade{position:absolute;inset:0;background:rgba(0,0,0,.35)}
.hero h1{position:absolute;left:0;width:1200px;top:160px;text-align:center;color:var(--white);font-weight:900;font-size:35px;line-height:47px;text-transform:uppercase}
.hero h1 em{font-style:normal;color:var(--green-bright)}
.hero p{position:absolute;left:300px;width:600px;top:268px;text-align:center;color:var(--white);font-size:17px;line-height:27px}
.hero .btn{position:absolute;left:463px;top:350px;width:292px;height:52px;font-size:17px}
.dots{position:absolute;display:flex;gap:14px}
.dots i{width:12px;height:12px;border-radius:50%;background:var(--white);display:block}
.dots i.on{background:var(--green-bright)}
/* welcome */
.welcome{position:absolute;left:0;top:675px;width:1200px;height:450px;background:var(--pale-blue)}
.welcome .kicker{left:153px;top:50px;font-size:28px;font-weight:900;color:var(--ink)}
.welcome h2{left:150px;top:88px;font-size:40px;font-weight:900;color:var(--navy);text-transform:uppercase}
.rule{position:absolute;height:3px;width:35px;background:var(--ink)}
.welcome p{left:153px;top:182px;width:460px;font-size:14.5px;line-height:21px;color:#222}
.welcome .btn{left:157px;top:355px;width:123px;height:37px;font-size:13px}
.welcome-photo{left:655px;top:48px;width:396px;height:350px;border-radius:16px;background:linear-gradient(135deg,#5a5a5c,#2e2f33 55%,#6b5a4c);overflow:hidden}
.badge{position:absolute;top:280px;height:46px;border-radius:23px;background:rgba(30,60,110,.75);display:flex;align-items:center;gap:12px;padding:0 18px 0 6px;color:var(--white);font-size:15px}
.badge b{width:38px;height:38px;border-radius:50%;background:var(--green);display:flex;align-items:center;justify-content:center}
/* section titles */
.sec-title{position:absolute;left:0;width:1200px;text-align:center;font-size:34px;font-weight:900;color:var(--ink);text-transform:uppercase}
.sec-title span{color:var(--navy)}
.center-rule{position:absolute;left:583px;width:34px;height:3px;background:var(--ink)}
/* programs */
.program{position:absolute;width:288px;height:313px;border-radius:12px;overflow:hidden}
.program h3{position:absolute;left:22px;bottom:18px;color:var(--white);font-weight:900;font-size:17px;text-transform:uppercase}
.program.featured h3{bottom:105px}
.program .fade{position:absolute;inset:0;background:linear-gradient(180deg,rgba(0,0,0,0) 55%,rgba(0,0,0,.65))}
.program.featured .fade{background:linear-gradient(180deg,rgba(29,143,107,.15) 30%,rgba(29,143,107,.95) 75%)}
.program .desc{position:absolute;left:24px;top:218px;width:240px;color:var(--white);font-size:12px;line-height:15px}
.program .mini{position:absolute;left:24px;top:265px;width:93px;height:25px;border-radius:13px;background:var(--white);color:var(--green);font-size:10px;font-weight:900;display:flex;align-items:center;justify-content:center}
/* join */
.join{position:absolute;left:0;top:1962px;width:1200px;height:405px;background:linear-gradient(120deg,#1c3a9a,#16318c 60%,#1d3fa2)}
.join .sec-title{color:var(--white);top:42px}
.city{position:absolute;top:149px;width:168px;text-align:center}
.city .ring{width:168px;height:168px;border-radius:50%;border:5px solid rgba(255,255,255,.35)}
.city .label{margin-top:18px;color:var(--white);font-size:18px;font-weight:700}
/* blog */
.blog-card{position:absolute;top:2515px;width:288px;height:396px;border-radius:12px;background:var(--white);box-shadow:0 4px 18px rgba(0,0,0,.08);overflow:hidden}
.blog-card .pic{height:203px}
.blog-card h4{margin:22px 26px 0 26px;font-size:16px;line-height:21px;color:var(--navy);font-weight:700}
.blog-card p{margin:12px 26px 0 26px;font-size:11.5px;line-height:16px;color:#333}
.blog-card .btn{margin:18px 0 0 26px;width:95px;height:28px;font-size:10px}
.blog-card.active{background:var(--green)}
.blog-card.active h4,.blog-card.active p{color:var(--white)}
.blog-card.active .btn{background:var(--white);color:var(--green)}
/* testimonials */
.quote{position:absolute;top:3113px;width:288px;height:242px;background:var(--white);border-radius:12px;box-shadow:0 4px 18px rgba(0,0,0,.08);padding:26px 28px}
.quote .who{display:flex;gap:14px;align-items:center}
.quote .av{width:42px;height:42px;border-radius:50%;background:linear-gradient(135deg,#777,#2b2b2b)}
.quote .name{font-size:12.5px;font-weight:900;color:var(--ink)}
.quote .loc{font-size:12px;color:#333;margin-top:2px}
.stars{margin-top:22px;display:flex;gap:2px}
.quote p{margin-top:18px;font-size:11.5px;line-height:18px;color:#333}
.tdots{position:absolute;left:551px;top:3391px;display:flex;gap:10px}
.tdots i{width:10px;height:10px;border-radius:50%;border:1.5px solid var(--green);display:block}
.tdots i.on{background:var(--green)}
/* newsletter */
.newsletter{position:absolute;left:0;top:3455px;width:1200px;height:532px;background:linear-gradient(180deg,#ffffff,#d4f0ea 30%,#e4f4f5 70%,#d5efe9)}
.nl-card{position:absolute;left:148px;top:68px;width:902px;height:417px;border-radius:20px;background:linear-gradient(90deg,#f1fbf9,#e3f5f2);box-shadow:0 8px 30px rgba(0,0,0,.12);overflow:hidden}
.nl-photo{position:absolute;left:0;top:0;width:404px;height:417px;background:linear-gradient(135deg,#4a4b4f,#222326 60%,#5a4b3e)}
.nl-card h2{position:absolute;left:458px;top:50px;font-size:30px;font-weight:900;color:var(--ink);text-transform:uppercase}
.nl-card h2 span{color:var(--navy)}
.nl-card .line{position:absolute;left:460px;top:102px;width:40px;height:3px;background:var(--green)}
.nl-card p{position:absolute;left:460px;top:126px;width:400px;font-size:14px;line-height:21px;color:#222}
.field{position:absolute;left:457px;width:382px;height:45px;border:1.5px solid var(--green);border-radius:23px;background:var(--white);font-size:12px;padding:15px 24px;color:#333}
.nl-card .submit{position:absolute;left:457px;top:322px;width:382px;height:50px;border-radius:25px;background:var(--navy);color:var(--white);font-size:21px;font-weight:900;display:flex;align-items:center;justify-content:center}
/* footer */
.site-footer{position:absolute;left:0;top:3987px;width:1200px;height:308px;background:var(--mint)}
.site-footer .brand{left:155px;top:92px}
.f-head{position:absolute;top:34px;font-size:15px;font-weight:900;color:var(--ink)}
.f-menu{position:absolute;left:441px;top:62px;font-size:12px;line-height:19.5px;color:#222;list-style:none}
.f-contact{position:absolute;left:600px;font-size:12px;color:#222;display:flex;gap:12px;line-height:17px}
.socials{position:absolute;left:865px;top:68px;display:flex;gap:5px}
.socials i{width:24px;height:24px;border-radius:50%;background:var(--navy);display:block}
.f-btn{position:absolute;left:862px;top:128px;width:189px;height:31px;font-size:10.5px}
.f-rule{position:absolute;left:148px;top:243px;width:902px;height:1px;background:#6aa79b}
.copy{position:absolute;left:0;width:1200px;top:261px;text-align:center;font-size:12px;color:#222}
</style>
</head>
<body>

<header class="site-header">
  <div class="abs brand">Corvane Athletics</div>
  <div class="abs search">Search
    <svg width="15" height="15" viewBox="0 0 15 15"><circle cx="6.5" cy="6.5" r="4.5" fill="none" stroke="#1d8f6b" stroke-width="1.5"/><line x1="10" y1="10" x2="13.5" y2="13.5" stroke="#1d8f6b" stroke-width="1.5"/></svg>
  </div>
  <div class="abs btn shop">Shop</div>
  <nav class="abs nav">
    <span class="active" style="left:0">ABOUT</span>
    <span style="left:77px">PROGRAMS</span>
    <span style="left:182px">LOCATIONS</span>
    <span style="left:287px">AFFILIATES</span>
    <span style="left:386px">BLOG</span>
    <span style="left:452px">MEMBERS</span>
    <span style="left:545px">CONTACT</span>
  </nav>
</header>

<section class="hero">
  <div class="abs" style="inset:0" role="img" aria-label="Athletes training with barbells and rings in a busy gym"></div>
  <div class="hero-shade"></div>
  <h1>Train with us at one of our Corvane<br>locations <em>across the country</em></h1>
  <p>Every location offers expert coaching, challenging group classes, and a supportive, driven community ready to help you thrive.</p>
  <div class="btn">Buy an online program</div>
  <div class="dots" style="left:552px;top:492px"><i class="on"></i><i></i><i></i><i></i></div>
</section>

<section class="welcome">
  <div class="abs kicker">WELCOME TO</div>
  <h2 class="abs">Corvane Athletics</h2>
  <div class="rule" style="left:153px;top:149px"></div>
  <p class="abs">Lorem ipsum dolor sit amet, consectetur adipiscing elit, sed do eiusmod tempor incididunt ut labore et dolore magna aliqua. Ut enim ad minim veniam, quis nostrud exercitation ullamco laboris nisi ut aliquip ex ea commodo consequat. Duis aute irure dolor in reprehenderit in voluptate velit esse cillum dolore eu fugiat nulla pariatur. Excepteur sint occaecat cupidatat non proident, sunt in culpa qui officia deserunt mollit anim id est laborum</p>
  <div class="abs btn">Read more</div>
  <div class="abs welcome-photo" role="img" aria-label="Athlete training hard on an air bike in a crowded gym">
    <div class="badge" style="left:22px"><b><svg width="20" height="20" viewBox="0 0 20 20" fill="#fff"><circle cx="10" cy="5" r="3"/><circle cx="4" cy="7" r="2"/><circle cx="16" cy="7" r="2"/><rect x="7" y="9" width="6" height="9" rx="2"/><rect x="2" y="10" width="4" height="7" rx="1.5"/><rect x="14" y="10" width="4" height="7" rx="1.5"/></svg></b>Expert Team</div>
    <div class="badge" style="left:204px"><b><svg width="20" height="20" viewBox="0 0 20 20" fill="#fff"><path d="M3 16c0-5 3-8 6-8l1-4 3 1-1 4c3 0 5 2 5 5v2z"/></svg></b>Best Coaching</div>
  </div>
</section>

<section>
  <h2 class="sec-title" style="top:1167px">Our <span>Programs</span></h2>
  <div class="center-rule" style="top:1232px"></div>

  <div class="program" style="left:150px;top:1267px;background:linear-gradient(135deg,#6a6660,#2f2d2c)" role="img" aria-label="Two athletes lifting together in a masters class"><div class="fade"></div><h3>Masters</h3></div>
  <div class="program featured" style="left:457px;top:1267px;background:linear-gradient(135deg,#4e5a55,#26312d)" role="img" aria-label="Athlete performing a ring muscle-up">
    <div class="fade"></div><h3>Functional Fitness</h3>
    <div class="desc">Lorem Ipsum is simply dummy text of the printing and typesetting industry</div>
    <div class="mini">READ MORE</div>
  </div>
  <div class="program" style="left:762px;top:1267px;background:linear-gradient(135deg,#8a8680,#3a3836)" role="img" aria-label="Competitive athlete standing in an arena"><div class="fade"></div><h3>Competitive</h3></div>
  <div class="program" style="left:150px;top:1602px;background:linear-gradient(135deg,#4f6a3a,#c9a64a 55%,#3c2a20)" role="img" aria-label="Healthy meal bowl with vegetables and grains"><div class="fade"></div><h3>Nutrition</h3></div>
  <div class="program" style="left:457px;top:1602px;background:linear-gradient(135deg,#5c5e62,#2a2b2e)" role="img" aria-label="Athlete lifting a loaded barbell"><div class="fade"></div><h3>Specialty</h3></div>
  <div class="program" style="left:762px;top:1602px;background:linear-gradient(135deg,#3a3b3f,#141416)" role="img" aria-label="Athlete skipping rope in a race hall"><div class="fade"></div><h3>Hybrid Race</h3></div>
</section>

<section class="join">
  <h2 class="sec-title">Join the Gym</h2>
  <div class="center-rule" style="top:106px;background:#fff"></div>
  <div class="city" style="left:144px"><div class="ring" role="img" aria-label="San Diego skyline" style="background:linear-gradient(180deg,#8fb6d9,#5c7b8f 60%,#4f7a45)"></div><div class="label">San Diego</div></div>
  <div class="city" style="left:334px"><div class="ring" role="img" aria-label="Boston skyline at sunset" style="background:linear-gradient(180deg,#e8a060,#b05a2e 55%,#2f2a2c)"></div><div class="label">Boston</div></div>
  <div class="city" style="left:518px"><div class="ring" role="img" aria-label="Miami marina and towers" style="background:linear-gradient(180deg,#7fb9e0,#c8d8de 55%,#2d8c95)"></div><div class="label">Miami</div></div>
  <div class="city" style="left:711px"><div class="ring" role="img" aria-label="Seattle skyline with tower" style="background:linear-gradient(180deg,#9fc8ea,#a8a69c 55%,#4e7a3e)"></div><div class="label">Seattle</div></div>
  <div class="city" style="left:894px"><div class="ring" role="img" aria-label="Capitol building in Washington DC" style="background:linear-gradient(180deg,#6e9fd6,#d9dde4 55%,#8a8f7a)"></div><div class="label">DC</div></div>
</section>

<section>
  <h2 class="sec-title" style="top:2410px">Latest <span>Blog</span></h2>
  <div class="center-rule" style="top:2477px"></div>

  <article class="blog-card active" style="left:150px">
    <div class="pic" role="img" aria-label="Athlete working with battle ropes" style="background:linear-gradient(135deg,#c9c9c9,#6b6b6b)"></div>
    <h4>Lorem ipsum dolor sit amet consectetur adipiscing</h4>
    <p>Lorem ipsum dolor sit amet, consec tetur adipiscing elit, sed do eiusmod tempor incididunt utveniam</p>
    <div class="btn">Read more</div>
  </article>
  <article class="blog-card" style="left:455px">
    <div class="pic" role="img" aria-label="Two athletes doing partner push-ups" style="background:linear-gradient(135deg,#7a7d82,#2e3034)"></div>
    <h4>Lorem ipsum dolor sit amet consectetur adipiscing</h4>
    <p>Lorem ipsum dolor sit amet, consec tetur adipiscing elit, sed do eiusmod tempor incididunt utveniam</p>
    <div class="btn">Read more</div>
  </article>
  <article class="blog-card" style="left:762px">
    <div class="pic" role="img" aria-label="Athlete swinging a kettlebell in chalk dust" style="background:linear-gradient(135deg,#3c3c3c,#0f0f0f)"></div>
    <h4>Lorem ipsum dolor sit amet consectetur adipiscing</h4>
    <p>Lorem ipsum dolor sit amet, consec tetur adipiscing elit, sed do eiusmod tempor incididunt utveniam</p>
    <div class="btn">Read more</div>
  </article>
</section>

<section>
  <h2 class="sec-title" style="top:3008px">Testimonials</h2>
  <div class="center-rule" style="top:3072px"></div>

  <div class="quote" style="left:-155px">
    <div class="who"><div class="av" role="img" aria-label="Reviewer portrait"></div><div><div class="name">DANA HOLLIS</div><div class="loc">United states</div></div></div>
    <div class="stars"><svg width="72" height="13" viewBox="0 0 72 13"><g fill="#1d8f6b"><path id="st" d="M6.5 0l1.6 4.3h4.4l-3.6 2.7 1.4 4.4-3.8-2.7-3.8 2.7 1.4-4.4L.5 4.3h4.4z"/><use href="#st" x="14.5"/><use href="#st" x="29"/><use href="#st" x="43.5"/><use href="#st" x="58"/></g></svg></div>
    <p>Sed ut perspiciatis unde omnis iste natus error sit voluptatem accusantium dolore mque laudantium, totam rem aperiam, eaque ipsa quae ab illo inventore veritatis et quasi architecto beatae vitae</p>
  </div>
  <div class="quote" style="left:150px">
    <div class="who"><div class="av" role="img" aria-label="Reviewer portrait"></div><div><div class="name">DANA HOLLIS</div><div class="loc">United states</div></div></div>
    <div class="stars"><svg width="72" height="13" viewBox="0 0 72 13"><g fill="#1d8f6b"><use href="#st"/><use href="#st" x="14.5"/><use href="#st" x="29"/><use href="#st" x="43.5"/><use href="#st" x="58"/></g></svg></div>
    <p>Sed ut perspiciatis unde omnis iste natus error sit voluptatem accusantium dolore mque laudantium, totam rem aperiam, eaque ipsa quae ab illo inventore veritatis et quasi architecto beatae vitae dicta sunt explicabo.</p>
  </div>
  <div class="quote" style="left:455px">
    <div class="who"><div class="av" role="img" aria-label="Reviewer portrait"></div><div><div class="name">DANA HOLLIS</div><div class="loc">United states</div></div></div>
    <div class="stars"><svg width="72" height="13" viewBox="0 0 72 13"><g fill="#1d8f6b"><use href="#st"/><use href="#st" x="14.5"/><use href="#st" x="29"/><use href="#st" x="43.5"/><use href="#st" x="58"/></g></svg></div>
    <p>Sed ut perspiciatis unde omnis iste natus error sit voluptatem accusantium dolore mque laudantium, totam rem aperiam, eaque ipsa quae ab illo inventore veritatis et quasi architecto beatae vitae dicta sunt explicabo.</p>
  </div>
  <div class="quote" style="left:762px">
    <div class="who"><div class="av" role="img" aria-label="Reviewer portrait"></div><div><div class="name">DANA HOLLIS</div><div class="loc">United states</div></div></div>
    <div class="stars"><svg width="72" height="13" viewBox="0 0 72 13"><g fill="#1d8f6b"><use href="#st"/><use href="#st" x="14.5"/><use href="#st" x="29"/><use href="#st" x="43.5"/><use href="#st" x="58"/></g></svg></div>
    <p>Sed ut perspiciatis unde omnis iste natus error sit voluptatem accusantium dolore mque laudantium, totam rem aperiam, eaque ipsa quae ab illo inventore veritatis et quasi architecto beatae vitae dicta sunt explicabo.</p>
  </div>
  <div class="quote" style="left:1067px">
    <div class="who"><div class="av" role="img" aria-label="Reviewer portrait"></div><div><div class="name">DANA HOLLIS</div><div class="loc">United states</div></div></div>
    <div class="stars"><svg width="72" height="13" viewBox="0 0 72 13"><g fill="#1d8f6b"><use href="#st"/><use href="#st" x="14.5"/><use href="#st" x="29"/><use href="#st" x="43.5"/><use href="#st" x="58"/></g></svg></div>
    <p>Sed ut perspiciatis unde omnis iste natus error sit voluptatem accusantium dolore mque laudantium, totam rem aperiam, eaque ipsa quae ab illo inventore veritatis et quasi architecto beatae vitae dicta sunt explicabo.</p>
  </div>
  <div class="tdots"><i class="on"></i><i></i><i></i><i></i><i></i></div>
</section>

<section class="newsletter">
  <div class="nl-card">
    <div class="nl-photo" role="img" aria-label="Athlete in a cap mid-workout with a jump rope"></div>
    <h2>Newsletter <span>Subscribe</span></h2>
    <div class="line"></div>
    <p>Lorem ipsum dolor sit amet, consec tetur adipiscing elit, sed do eiusmod tempor incididunt utveniam</p>
    <div class="field" style="top:197px">Full Name</div>
    <div class="field" style="top:255px">Email id</div>
    <div class="submit">SUBSCRIBE</div>
  </div>
</section>

<footer class="site-footer">
  <div class="abs brand">Corvane Athletics</div>
  <div class="f-head" style="left:441px">MENU</div>
  <ul class="f-menu"><li>About</li><li>Programs</li><li>Locations</li><li>Affiliates</li><li>Blog</li><li>Members</li><li>Contact</li></ul>
  <div class="f-head" style="left:600px">CONTACT US</div>
  <div class="f-contact" style="top:62px"><svg width="13" height="16" viewBox="0 0 13 16"><path d="M6.5 0A6 6 0 0 0 .5 6c0 4.5 6 10 6 10s6-5.5 6-10a6 6 0 0 0-6-6z" fill="#1b3a9c"/><circle cx="6.5" cy="6" r="2.2" fill="#b7e7de"/></svg><span>402 Harlow Park Rd. Suite 2-210<br>Bellmont, TN 37190</span></div>
  <div class="f-contact" style="top:121px"><svg width="14" height="14" viewBox="0 0 14 14"><path d="M3 0l3 3-2 2c1 2 3 4 5 5l2-2 3 3-2 3C6 14 0 8 0 2z" fill="#1b3a9c"/></svg><span>+1 555 014 2290</span></div>
  <div class="f-contact" style="top:157px"><svg width="15" height="12" viewBox="0 0 15 12"><rect width="15" height="12" rx="1.5" fill="#1b3a9c"/><path d="M1 1.5l6.5 5 6.5-5" fill="none" stroke="#b7e7de" stroke-width="1.3"/></svg><span>info@corvaneathletics.com</span></div>
  <div class="f-head" style="left:865px">FOLLOW US</div>
  <div class="socials"><i></i><i></i><i></i><i></i><i></i></div>
  <div class="btn f-btn">Buy an online program</div>
  <div class="f-rule"></div>
  <div class="copy">Copyright © 2025 All Rights Reserved</div>
</footer>

</body>
</html>
```